Valdane Companies Business Card Design

We need a new business card for our Private Equity Real Estate Development firm, “Valdane” and our EB-5 regional center “Thornmere Regional Center” on one card. We prefer a design that is simple, elegant, and represents the luxury products we design and build as well as the financial security and stability our successful history has produced. We are an industry leader in our field and 3rd generation family business that has evolved into an institutional quality investment platform. Considered design size is standard business card dimensions (3.5 x 2 inches with an additional 1/8 inch space for design elements or backgrounds that extend beyond the finished size of your piece.

Target Market(s)

• High net worth individuals
• Highly skilled technical workers and physicians in the US seeking investment-based immigration opportunities
• Sophisticated private equity investors
• Intermediary partners include domestic attorneys and investment brokers, as well as international agent networks
• US real estate developers

Industry/Entity Type

Finance

Contact Information for Business Card

(Providing placeholder info for personal information, please design for longer character spaces, longer names and addresses etc..)
• Logo for Valdane
• Logo for Thornmere Regional Center
• Full name: Marcus Valdane
• Job title: CEO
• Email address: mvaldane@valdanecompanies.com
• Cell phone number: +1.555.314.2287
• Office number +1.555.628.4410
• Office address: Larkfield Court 5, 4817 Vista Orilla, Alder Vale, OR.
• Website: www.valdanecompanies.com

Font styles to use
Serif
Sans Serif

Colors
ec1f27
ffffff
000000

Requirements
Must have
• • Logo for Valdane
• • Logo for Thornmere Regional Center
• - Use rounded corners
• (See .ai file included for logos)
Nice to have
• • Simple, elegant design
• • Aesthetically compatible with our website design (www.valdanecompanies.com)
• • Color palette including but not limited to white, black, and red (as per logos)
Should not have
• - Not too much red color
• - Do not stack both logos on top of each other

```html
<!DOCTYPE html>
<html lang="en">
<head>
<meta charset="utf-8">
<title>Valdane Companies – Business Card</title>
<link href="https://fonts.googleapis.com/css2?family=Cinzel:wght@700&family=Roboto:wght@400;700&display=swap" rel="stylesheet">
<style>
  :root {
    --page: #151515;
    --card: #2a2a2b;
    --red: #ec1f27;
    --white: #ffffff;
    --black: #000000;
    --muted: #d9d9d9;
  }
  * { margin: 0; padding: 0; box-sizing: border-box; }
  html, body { width: 1200px; height: 1200px; overflow: hidden; background: var(--page); }
  body {
    display: flex; flex-direction: column; align-items: center; justify-content: center;
    gap: 44px; font-family: "Roboto", Arial, sans-serif;
  }
  .card {
    position: relative; width: 900px; height: 514px;
    background: var(--card); border-radius: 18px; overflow: hidden;
    border-bottom: 6px solid var(--red);
  }
  /* Back */
  .card-back .brand {
    position: absolute; left: 430px; top: 250px;
    display: flex; align-items: center; gap: 22px;
  }
  .brand-mark { width: 26px; height: 26px; background: var(--white); }
  .brand-name {
    font-family: "Cinzel", Georgia, serif; font-weight: 700; color: var(--white);
    line-height: 1; letter-spacing: 2px;
  }
  .card-back .brand-name { font-size: 42px; }
  .brand-name .sub { display: block; font-size: 14px; letter-spacing: 8px; margin-top: 8px; }

  /* Front */
  .card-front .brand {
    position: absolute; left: 60px; top: 200px;
    display: flex; flex-direction: column; align-items: flex-start; gap: 18px;
  }
  .card-front .brand-mark { width: 40px; height: 40px; background: var(--red); }
  .card-front .brand-name { color: var(--red); font-size: 50px; }
  .card-front .brand-name .sub { font-size: 16px; letter-spacing: 9px; margin-top: 12px; }
  .divider {
    position: absolute; left: 478px; top: 120px; width: 2px; height: 270px; background: var(--white);
  }
  .contact { position: absolute; left: 512px; top: 122px; color: var(--white); }
  .contact .name { color: var(--red); font-weight: 700; font-size: 30px; line-height: 1.1; }
  .contact .title { font-weight: 700; font-size: 21px; margin-top: 4px; }
  .contact .address { font-size: 17px; line-height: 1.3; margin-top: 10px; color: var(--muted); }
  .contact ul { list-style: none; margin-top: 14px; }
  .contact li {
    display: flex; align-items: center; gap: 14px;
    font-size: 17px; line-height: 1.55; color: var(--muted);
  }
  .contact svg { width: 16px; height: 16px; flex: none; }
</style>
</head>
<body>
  <section class="card card-back" aria-label="Card back">
    <div class="brand">
      <span class="brand-mark"></span>
      <span class="brand-name">THORNMERE<span class="sub">CENTER</span></span>
    </div>
  </section>

  <section class="card card-front" aria-label="Card front">
    <div class="brand">
      <span class="brand-mark"></span>
      <span class="brand-name">THORNMERE<span class="sub">REGIONAL CENTER</span></span>
    </div>
    <div class="divider"></div>
    <div class="contact">
      <p class="name">Marcus Valdane</p>
      <p class="title">CEO</p>
      <p class="address">Larkfield Court 5, 4817<br>Vista Orilla Alder Vale, OR</p>
      <ul>
        <li>
          <svg viewBox="0 0 16 16"><rect x="4" y="1" width="8" height="14" rx="1.5" fill="none" stroke="#ec1f27" stroke-width="1.6"/><circle cx="8" cy="12.5" r="0.9" fill="#ec1f27"/></svg>
          +1.555.314.2287
        </li>
        <li>
          <svg viewBox="0 0 16 16"><path d="M2 6c0-2 3-3 6-3s6 1 6 3v1h-3V5.5H5V7H2z" fill="#ec1f27"/><rect x="3" y="8" width="10" height="6" rx="1" fill="#ec1f27"/></svg>
          +1.555.628.4410
        </li>
        <li>
          <svg viewBox="0 0 16 16"><rect x="1" y="3" width="14" height="10" fill="#ec1f27"/><path d="M1 3l7 6 7-6" fill="none" stroke="#2a2a2b" stroke-width="1.3"/></svg>
          mvaldane@valdanecompanies.com
        </li>
        <li>
          <svg viewBox="0 0 16 16"><circle cx="8" cy="8" r="6.5" fill="none" stroke="#ec1f27" stroke-width="1.5"/><ellipse cx="8" cy="8" rx="2.8" ry="6.5" fill="none" stroke="#ec1f27" stroke-width="1.2"/><path d="M1.5 8h13" stroke="#ec1f27" stroke-width="1.2"/></svg>
          www.valdanecompanies.com
        </li>
      </ul>
    </div>
  </section>
</body>
</html>
```